NEW Modern Sleek Business Card for VR Language Startup

Our startup is using VR to lead the next wave of world language education. We need a two-sided business card that introduces the larger organization (Brightloom Language Inc) and our contact info on one side and shows the product, Glimwoorld, on the other side.

Side 1 (contact info)= Brightloom Logo and Contact info (name, title, phone, email)

Side 2 (product)= Glimworld logo, text, and website
Text= Culturally Immersive Language Learning Games
Website= www.glimworld-play.com

Target Market(s)

Education, Technology

Contact Information for Business Card

Contact info will be updated upon approval of the design. For now, put this as a placeholder.

Perry Dunmore
Founder & CEO
pdunmore@quillpost-mail.net
(555)-014-2286

Font styles to use
Other font styles liked:
• Gibson and Century Gothic are the brand fonts

Requirements
Nice to have
• I would love to see cohesion between the design and colors of the two logos. I have attached a few business card designs that I like, so you can get a feel for my preferred style.

```html
<!DOCTYPE html>
<html lang="en">
<head>
<meta charset="utf-8">
<title>Brightloom Language – Business Card</title>
<link href="https://fonts.googleapis.com/css2?family=Lato:wght@400;700;900&display=swap" rel="stylesheet">
<style>
  :root {
    --stage: #1b1b1d;
    --card-light: #ffffff;
    --card-dark: #151515;
    --ink-grey: #3d3d3d;
    --rule-light: #d6d6d6;
    --rule-dark: #555555;
    --link-blue: #3b8cf0;
    --brand-blue: #2f7df0;
    --text-white: #ffffff;
    --grad-orange: #ff8a2a;
    --grad-pink: #ff3f8e;
    --grad-violet: #8a5cf6;
    --icon-coral: #ff6a4d;
  }
  * { margin: 0; padding: 0; box-sizing: border-box; }
  html, body {
    width: 1200px; height: 900px; overflow: hidden;
    background: var(--stage);
    font-family: "Lato", Arial, sans-serif;
  }
  .stage {
    position: relative; width: 1200px; height: 900px;
    display: flex; flex-direction: column; align-items: center; justify-content: center; gap: 48px;
  }
  .card {
    width: 620px; height: 354px; border-radius: 6px; position: relative;
    box-shadow: 0 18px 40px rgba(0,0,0,.55);
  }

  /* Product side */
  .card--product {
    background: var(--card-light);
    display: flex; flex-direction: column; align-items: center; justify-content: center;
  }
  .product-mark {
    display: flex; align-items: center; gap: 16px; margin-bottom: 26px;
  }
  .product-mark__dot {
    width: 46px; height: 46px; border-radius: 50%; background: var(--brand-blue);
  }
  .product-mark__name {
    font-size: 52px; font-weight: 700; color: var(--brand-blue); letter-spacing: .5px;
  }
  .product-tagline {
    width: 420px; text-align: center;
    border-top: 1px solid var(--rule-light); border-bottom: 1px solid var(--rule-light);
    padding: 12px 0; font-size: 15px; color: var(--ink-grey); letter-spacing: .4px;
  }
  .product-web {
    margin-top: 14px; font-size: 17px; color: var(--link-blue); letter-spacing: 1px;
  }

  /* Contact side */
  .card--contact {
    background: var(--card-dark);
    display: flex; align-items: center;
  }
  .org-block {
    width: 310px; display: flex; flex-direction: column; align-items: center; gap: 18px;
  }
  .org-block__dot {
    width: 70px; height: 70px; border-radius: 50%;
    background: linear-gradient(135deg, var(--grad-orange), var(--grad-pink), var(--grad-violet));
  }
  .org-block__name {
    font-size: 30px; font-weight: 700; color: var(--text-white);
    letter-spacing: 3px; text-align: center; line-height: 1.15;
  }
  .divider {
    width: 1px; height: 230px; background: var(--rule-dark);
  }
  .contact-block {
    padding-left: 36px; color: var(--text-white);
  }
  .contact-name {
    font-size: 27px; font-weight: 700; letter-spacing: .5px;
    background: linear-gradient(90deg, var(--grad-orange), var(--grad-pink) 55%, var(--grad-violet));
    -webkit-background-clip: text; background-clip: text; color: transparent;
  }
  .contact-title { font-size: 19px; margin-top: 2px; margin-bottom: 20px; }
  .contact-line {
    display: flex; align-items: center; gap: 10px; font-size: 17px; margin-top: 6px;
  }
  .contact-line svg { flex: none; }
</style>
</head>
<body>
<main class="stage">

  <section class="card card--product" aria-label="Product side">
    <div class="product-mark">
      <span class="product-mark__dot"></span>
      <span class="product-mark__name">Glimworld</span>
    </div>
    <p class="product-tagline">CULTURALLY IMMERSIVE LANGUAGE LEARNING GAMES</p>
    <p class="product-web">www.glimworld-play.com</p>
  </section>

  <section class="card card--contact" aria-label="Contact side">
    <div class="org-block">
      <span class="org-block__dot"></span>
      <span class="org-block__name">BRIGHTLOOM<br>LANGUAGE</span>
    </div>
    <div class="divider"></div>
    <div class="contact-block">
      <p class="contact-name">PERRY DUNMORE</p>
      <p class="contact-title">Founder &amp; CEO</p>
      <p class="contact-line">
        <svg width="18" height="16" viewBox="0 0 18 16" aria-hidden="true">
          <path d="M2 5 Q9 0 16 5 L14 7 L12 5 L6 5 L4 7 Z" fill="var(--icon-coral)"/>
          <rect x="3" y="8" width="12" height="7" rx="1.5" fill="var(--icon-coral)"/>
          <circle cx="9" cy="11.5" r="1.8" fill="var(--card-dark)"/>
        </svg>
        (555)-014-2286
      </p>
      <p class="contact-line">
        <svg width="18" height="14" viewBox="0 0 18 14" aria-hidden="true">
          <rect x="1" y="1" width="16" height="12" rx="1.5" fill="var(--icon-coral)"/>
          <path d="M1.5 2 L9 8 L16.5 2" stroke="var(--card-dark)" stroke-width="1.4" fill="none"/>
        </svg>
        pdunmore@quillpost-mail.net
      </p>
    </div>
  </section>

</main>
</body>
</html>
```